Corvane Business Cards

Front of business card will have logo, name, address, & telephone number. Back of card will have a list of services provided - Roads, Substation Pads, Temporary Pads, Site Pads, Land Leveling, Powerline Row Cleaning, Land Clearing, Gates, Fencing, Construction Entrances, Excavation, Trenching, Underground Utilities, Directional Boring, Pile Driving. We are a construction company that uses heavy equipment like bulldozers, motor graders/blades, dump trucks, backhoes, hydro axes, & skid loaders. We build roads, pads, & install electric utility lines & waterlines underground. This logo is new. The word "Construction" can be smaller as uploaded 2 example edited logos. We will be using this card design for many employees.
Target Market(s)
Industrial Electric Powerline, Wind Turbine, Solar Panel, & Water Utility companies.
Contact Information for Business Card
Name/Position - Dwayne Halster - Owner
Address: 4875 FM 309
Dunmore, TX 79412
Phone number - (325) 482-5096

```html
<!DOCTYPE html>
<html lang="en">
<head>
<meta charset="utf-8">
<title>Corvane Construction Business Cards</title>
<link href="https://fonts.googleapis.com/css2?family=Montserrat:wght@700&family=Roboto:wght@400;500&display=swap" rel="stylesheet">
<style>
  :root {
    --maroon: #3d111c;
    --maroon-ink: #3b1019;
    --paper: #ffffff;
    --grey-text: #555555;
    --backdrop: #d9d9d9;
  }
  * { margin: 0; padding: 0; box-sizing: border-box; }
  html, body { width: 1200px; height: 900px; overflow: hidden; }
  body {
    background: var(--backdrop);
    font-family: "Roboto", sans-serif;
    display: flex;
    flex-direction: column;
    align-items: center;
    justify-content: center;
    gap: 40px;
  }
  .card {
    width: 700px;
    height: 400px;
    box-shadow: 0 6px 18px rgba(0,0,0,0.25);
    position: relative;
    flex: none;
  }

  /* Services side */
  .card--services {
    background: var(--maroon);
    color: var(--paper);
    display: flex;
    flex-direction: column;
    align-items: center;
    justify-content: center;
    gap: 44px;
  }
  .services-brand {
    display: flex;
    align-items: center;
    gap: 14px;
    font-weight: 500;
    font-size: 58px;
    letter-spacing: 2px;
    line-height: 1;
    color: var(--paper);
  }
  .brand-square {
    width: 26px;
    height: 26px;
    background: var(--paper);
  }
  .services-list {
    text-align: center;
    font-size: 16px;
    line-height: 1.6;
    letter-spacing: 0.2px;
    white-space: nowrap;
  }
  .services-list .sep { margin: 0 6px; }

  /* Contact side */
  .card--contact {
    background: var(--paper);
    display: flex;
    align-items: center;
    padding: 0 40px 0 60px;
  }
  .contact-brand {
    width: 270px;
    flex: none;
    color: var(--maroon-ink);
    font-weight: 500;
    text-align: center;
    line-height: 1.1;
    margin-top: 90px;
  }
  .contact-brand .brand-name { display: block; font-size: 44px; letter-spacing: 2px; }
  .contact-brand .brand-line { display: block; font-size: 24px; letter-spacing: 3px; margin-top: 6px; }
  .divider {
    width: 1px;
    height: 150px;
    flex: none;
    background: var(--maroon-ink);
    margin: 20px 30px 0 26px;
  }
  .contact-details {
    color: var(--grey-text);
    font-size: 18px;
    line-height: 1.45;
    white-space: nowrap;
    margin-top: -40px;
  }
  .contact-name {
    font-family: "Montserrat", sans-serif;
    font-weight: 700;
    font-size: 26px;
    color: var(--maroon-ink);
    letter-spacing: 0.5px;
    line-height: 1.2;
  }
  .contact-phone { display: flex; align-items: center; gap: 8px; }
  .phone-icon { width: 20px; height: 20px; flex: none; }
</style>
</head>
<body>
  <section class="card card--services">
    <div class="services-brand"><span class="brand-square"></span>CORVANE</div>
    <p class="services-list">
      Roads<span class="sep">|</span>Substation Pads<span class="sep">|</span>Temporary Pads<span class="sep">|</span>Site Pads<span class="sep">|</span>Land Leveling<br>
      Land Clearing<span class="sep">|</span>Gates<span class="sep">|</span>Fencing<span class="sep">|</span>Construction Entrances<span class="sep">|</span>Excavation<span class="sep">|</span>Trenching<br>
      Underground Utilities<span class="sep">|</span>Powerline Row Cleaning<span class="sep">|</span>Pile Driving<span class="sep">|</span>Directional Boring
    </p>
  </section>

  <section class="card card--contact">
    <div class="contact-brand">
      <span class="brand-name">CORVANE</span>
      <span class="brand-line">CONSTRUCTION</span>
    </div>
    <div class="divider"></div>
    <div class="contact-details">
      <p class="contact-name">Dwayne Halster</p>
      <p>Owner</p>
      <p>4875 FM 309</p>
      <p>Dunmore, TX 79412</p>
      <p class="contact-phone">
        <svg class="phone-icon" viewBox="0 0 20 20" aria-hidden="true">
          <circle cx="10" cy="10" r="10" fill="#3b1019"/>
          <path d="M7 5.5c.4 0 .7.2.8.5l.6 1.6c.1.3 0 .6-.2.8l-.7.6c.5 1 1.3 1.8 2.3 2.3l.6-.7c.2-.2.5-.3.8-.2l1.6.6c.3.1.5.4.5.8v1.2c0 .5-.4.9-.9.9C8.8 13.9 6.1 11.2 6 7.3c0-.5.4-.9.9-.9z" fill="#ffffff"/>
        </svg>
        (325) 482-5096
      </p>
    </div>
  </section>
</body>
</html>
```